Dawn Ledger

Full Color 1/8 page newspaper ad . We are 1 stop shop for all mobility needs. Highlight Accessible Van Rentals & Sales. 50 free miles on your rental when you mention this ad.

```html
<!DOCTYPE html>
<html lang="en">
<head>
<meta charset="utf-8">
<title>Summit Ride Mobility – Accessible Van Rentals &amp; Sales</title>
<link rel="stylesheet" href="https://fonts.googleapis.com/css2?family=Nunito:wght@300;400;700;800;900&display=swap">
<style>
  :root {
    --navy: #29245f;
    --ink: #1f1f1f;
    --white: #ffffff;
    --sky: #a9cdea;
    --rule: #a6c6e6;
    --photo-light: #e9eaec;
    --photo-mid: #b9bcc2;
  }
  * { box-sizing: border-box; margin: 0; padding: 0; }
  html, body { width: 1200px; height: 809px; overflow: hidden; background: var(--white); }
  .ad {
    position: relative; width: 1200px; height: 809px;
    background: var(--white); border: 1px solid var(--navy);
    font-family: "Nunito", sans-serif; color: var(--ink);
  }
  .top-band {
    position: absolute; left: 0; top: 0; width: 1200px; height: 230px;
    background: var(--navy); color: var(--white);
  }
  .headline {
    position: absolute; left: 38px; top: 14px;
    font-size: 74px; font-weight: 900; letter-spacing: 0.5px; line-height: 1.1;
  }
  .subhead {
    position: absolute; left: 38px; top: 104px;
    font-size: 40px; line-height: 54px; font-weight: 300; letter-spacing: 1px;
  }
  .subhead strong { font-weight: 800; }
  .van-photo {
    position: absolute; left: 603px; top: 165px; width: 572px; height: 290px;
    border-radius: 40px 60px 30px 30px;
    background: radial-gradient(ellipse at 60% 55%, var(--photo-mid), var(--photo-light) 75%, rgba(255,255,255,0) 100%);
  }
  .intro {
    position: absolute; left: 37px; top: 244px; width: 610px;
    font-size: 20px; line-height: 30px; font-weight: 400;
  }
  .offer-badge { position: absolute; left: 705px; top: 345px; width: 130px; height: 130px; }
  .offer-text {
    position: absolute; left: 713px; top: 372px; width: 114px;
    transform: rotate(-10deg); text-align: center;
    font-size: 12.5px; line-height: 15px; font-weight: 800; color: var(--ink);
  }
  .range-title {
    position: absolute; left: 37px; top: 420px;
    font-size: 30px; font-weight: 800; color: var(--navy);
  }
  .range-rule { position: absolute; left: 0; top: 466px; width: 630px; height: 2px; background: var(--rule); }
  .product { position: absolute; top: 477px; text-align: center; }
  .product-photo { height: 190px; border-radius: 10px; background: linear-gradient(180deg, #d8d9de, #f2f2f4); }
  .product-label {
    margin-top: 17px; font-size: 18px; line-height: 25px; font-weight: 800;
    color: var(--navy); letter-spacing: 0.3px;
  }
  .brand {
    position: absolute; left: 781px; top: 490px; width: 395px; text-align: center;
    font-size: 38px; line-height: 42px; font-weight: 900; color: var(--navy);
  }
  .website {
    position: absolute; left: 781px; top: 603px; width: 395px; text-align: center;
    font-size: 17px; font-weight: 800; letter-spacing: 2px; color: var(--ink);
  }
  .phones {
    position: absolute; left: 781px; top: 632px; width: 395px; text-align: center;
    font-size: 39px; line-height: 47px; font-weight: 800; color: var(--ink);
  }
  .bottom-band {
    position: absolute; left: 0; top: 736px; width: 1198px; height: 71px;
    background: var(--navy); color: var(--white);
    display: flex; align-items: center; justify-content: center;
    font-size: 27px; font-weight: 800; letter-spacing: 9.4px;
  }
</style>
</head>
<body>
<div class="ad">
  <header class="top-band">
    <h1 class="headline">Let’s Maximize Your Mobility!</h1>
    <p class="subhead"><strong>BUY OR RENT</strong> ONE OF OUR WELL MAINTAINED<br><strong>ACCESSIBLE VANS</strong></p>
  </header>

  <div class="van-photo" role="img" aria-label="Silver accessible minivan with side ramp and a man in a power wheelchair"></div>

  <p class="intro">We know that travel can be difficult with mobility devices, so that’s why we rent out accessible vans! This is a great opportunity to get a loved one out of the house, or even to a doctor’s appointment! We are committed to making mobility and accessibility a breeze!</p>

  <svg class="offer-badge" viewBox="0 0 130 130" aria-hidden="true">
    <polygon fill="#a9cdea" points="65,2 73,16 87,6 90,22 106,17 103,33 120,33 112,48 127,55 115,66 127,77 112,83 119,99 102,99 104,115 89,110 85,126 72,116 65,128 57,116 44,126 40,110 25,115 27,99 10,99 17,83 3,77 15,66 3,55 17,48 10,33 27,33 24,17 40,22 43,6 57,16"/>
  </svg>
  <p class="offer-text">50 free miles on your rental when you mention this ad</p>

  <h2 class="range-title">Our other Access &amp; Mobility range</h2>
  <div class="range-rule"></div>

  <div class="product" style="left:35px;width:160px;">
    <div class="product-photo" role="img" aria-label="Red four-wheel mobility scooter with basket"></div>
    <p class="product-label">MOBILITY<br>SCOOTER</p>
  </div>
  <div class="product" style="left:230px;width:135px;">
    <div class="product-photo" role="img" aria-label="Knee scooter with handlebars"></div>
    <p class="product-label">MOBILITY<br>SCOOTER</p>
  </div>
  <div class="product" style="left:403px;width:131px;">
    <div class="product-photo" role="img" aria-label="Rolling walker with seat"></div>
    <p class="product-label">WALKING<br>AIDS</p>
  </div>
  <div class="product" style="left:584px;width:146px;">
    <div class="product-photo" role="img" aria-label="Black and blue power wheelchair"></div>
    <p class="product-label">POWER<br>WHEELCHAIR</p>
  </div>

  <p class="brand">SUMMIT RIDE<br>MOBILITY</p>
  <p class="website">www.summitridemobility.com</p>
  <p class="phones">(307) 555-0148<br>(970) 555-0192</p>

  <footer class="bottom-band">The one stop shop for all of your mobility needs</footer>
</div>
</body>
</html>
```